Envelope Design - Winner can do follow-up business

- Varnoko.com is a Swiss-based online store selling business shirts and accessories for business men
- Please visit the webpage to make yourself familiar with the company. Although the text is in German, with Plimbo translator you should be able to understand the main content.
- Our clients are mainly business men between 30 and 60 years old. Mostly with a high income working in the service industry (banking, insurance, lawyers, etc.). Sometimes there wives purchase the shirts for them ;-)
- The colors and the logo are given, as they are also used for the print materials (please see files in attachment)
- I am running several businesses and often need a talented web designer --> the winner gets substantial follow-up business
your task:
-for our company we need a new envelope design
-It should be simple and modern
-please use one of the logos in the followings.
-suprise me :)

```html
<!DOCTYPE html>
<html lang="en">
<head>
<meta charset="utf-8">
<title>Varnoko Envelope</title>
<link rel="stylesheet" href="https://fonts.googleapis.com/css2?family=Michroma&family=Roboto:wght@400&display=swap">
<style>
  :root {
    --backdrop: #e9e9ea;
    --paper: #ffffff;
    --ink: #0b0b0b;
    --brand-red: #e0231c;
    --brand-yellow: #ecd64f;
    --brand-gold: #e6c13a;
    --window: #b5b5b5;
    --window-edge: #9a9a9a;
    --blush: #f6c9c9;
  }
  html, body {
    margin: 0;
    width: 1200px;
    height: 928px;
    overflow: hidden;
    background: var(--backdrop);
  }
  .canvas {
    position: relative;
    width: 1200px;
    height: 928px;
  }
  .envelope {
    position: absolute;
    left: 220px;
    width: 760px;
    height: 380px;
    background: var(--paper);
    box-shadow: 0 2px 8px rgba(0,0,0,0.12);
  }
  .envelope--front { top: 50px; }
  .envelope--back { top: 490px; }
  .envelope svg { display: block; }
  .brand-name {
    font-family: "Michroma", sans-serif;
    font-size: 26px;
    letter-spacing: 4px;
    fill: var(--brand-gold);
  }
  .contact-line {
    font-family: "Roboto", sans-serif;
    font-size: 8.5px;
    fill: var(--ink);
  }
</style>
</head>
<body>
<main class="canvas">

  <section class="envelope envelope--front" aria-label="Envelope front">
    <svg width="760" height="380" viewBox="0 0 760 380">
      <defs>
        <linearGradient id="blushFade" x1="0" y1="0" x2="1" y2="1">
          <stop offset="0" stop-color="var(--blush)" stop-opacity="0.55"/>
          <stop offset="1" stop-color="var(--blush)" stop-opacity="0"/>
        </linearGradient>
      </defs>
      <rect class="header-band" x="0" y="0" width="760" height="95" fill="var(--ink)"/>
      <rect class="pattern-area" x="470" y="95" width="240" height="170" fill="url(#blushFade)" role="img" aria-label="Faint brand pattern area"/>
      <text class="brand-name" x="38" y="56">VARNOKO</text>
      <rect class="address-window" x="70" y="78" width="220" height="82" rx="14" fill="var(--window)" stroke="var(--window-edge)"/>
      <line class="rule" x1="0" y1="163" x2="760" y2="296" stroke="var(--ink)" stroke-width="2"/>
      <polygon class="stripe stripe--red" points="0,172 292,223 300,244 0,192" fill="var(--brand-red)"/>
      <polygon class="stripe stripe--yellow" points="298,224 760,305 760,325 306,245" fill="var(--brand-yellow)"/>
      <line class="rule" x1="320" y1="256" x2="760" y2="333" stroke="var(--ink)" stroke-width="2"/>
    </svg>
  </section>

  <section class="envelope envelope--back" aria-label="Envelope back">
    <svg width="760" height="380" viewBox="0 0 760 380">
      <path class="flap" d="M330,0 H760 V165 Q758,200 715,188 Q540,130 365,45 Q338,28 330,0 Z" fill="var(--ink)"/>
      <rect class="pattern-area" x="420" y="170" width="200" height="120" fill="var(--blush)" opacity="0.3" role="img" aria-label="Faint brand pattern area"/>
      <polygon class="stripe stripe--red" points="0,178 320,234 326,250 0,194" fill="var(--brand-red)"/>
      <polygon class="stripe stripe--yellow" points="372,244 760,312 760,328 378,260" fill="var(--brand-yellow)"/>
      <text class="contact-line" x="300" y="218" transform="rotate(9.9 300 218)">Varnoko GmbH | Lindenweg 21 8400 Winterthur | T: +41 52 000 14 37 | E: info@varnoko.com</text>
    </svg>
  </section>

</main>
</body>
</html>
```